Executive recruiting firm in need of business card design

Executive recruiting firm looking for a sleek, classy and modern business card design; card itself will be square shape, rounded edges and soft touch paper, our colors are dark blues in the navy color scale, silvers and grays. Reference our website for a better idea of our company's feel and goals at Tarvex-Up.com - our company message is "Employee Engagement Begins at Recruitment" this should be on the card

```html
<!DOCTYPE html>
<html lang="en">
<head>
<meta charset="utf-8">
<title>Tarvex-Up business cards</title>
<link rel="stylesheet" href="https://fonts.googleapis.com/css2?family=Arimo:wght@400;700&display=swap">
<style>
  :root {
    --backdrop: #efefef;
    --card: #ffffff;
    --card-edge: #e2e2e2;
    --navy: #3a3b63;
    --slate: #8a8ca3;
    --ink: #2b2b3a;
  }
  html, body {
    margin: 0;
    width: 1200px;
    height: 1000px;
    overflow: hidden;
    background: var(--backdrop);
    font-family: "Arimo", Arial, sans-serif;
  }
  .canvas { position: relative; width: 1200px; height: 1000px; }
  .card {
    position: absolute;
    background: var(--card);
    border: 1px solid var(--card-edge);
    box-sizing: border-box;
  }
  .card--front { left: 501px; top: 153px; width: 500px; height: 324px; }
  .card--back  { left: 232px; top: 520px; width: 502px; height: 325px; }

  .brand { position: absolute; }
  .brand__name {
    display: block;
    color: var(--navy);
    font-weight: 400;
    white-space: nowrap;
    line-height: 1;
  }
  .brand__tagline {
    display: block;
    color: var(--slate);
    white-space: nowrap;
    line-height: 1;
  }

  .card--front .brand { left: 142px; top: 146px; }
  .card--front .brand__name { font-size: 34px; letter-spacing: 3px; }
  .card--front .brand__tagline { font-size: 8px; letter-spacing: 1px; margin-top: 9px; }

  .card--back .brand { left: 290px; top: 80px; }
  .card--back .brand__name { font-size: 24px; letter-spacing: 2px; }
  .card--back .brand__tagline { font-size: 6.5px; letter-spacing: 0.6px; margin-top: 7px; }

  .holder { position: absolute; left: 50px; top: 77px; color: var(--ink); font-size: 17px; line-height: 21px; }
  .holder__name strong { font-weight: 700; }

  .contacts { position: absolute; left: 306px; top: 236px; margin: 0; padding: 0; list-style: none; }
  .contacts li {
    display: flex; align-items: center; gap: 8px;
    height: 20.5px; font-size: 12.5px; color: var(--ink);
  }
  .contacts svg { width: 14px; height: 14px; stroke: var(--ink); fill: none; stroke-width: 1.3; }
</style>
</head>
<body>
<main class="canvas">
  <section class="card card--front" aria-label="Card front">
    <div class="brand">
      <span class="brand__name">TARVEX UP</span>
      <span class="brand__tagline">Employee Engagement Begins at Recruitment</span>
    </div>
  </section>

  <section class="card card--back" aria-label="Card back">
    <div class="holder">
      <div class="holder__name">Loresum <strong>ipsum</strong></div>
      <div class="holder__title">Président</div>
    </div>
    <div class="brand">
      <span class="brand__name">TARVEX UP</span>
      <span class="brand__tagline">Employee Engagement Begins at Recruitment</span>
    </div>
    <ul class="contacts">
      <li>
        <svg viewBox="0 0 14 14" aria-hidden="true"><circle cx="7" cy="7" r="6"/><path d="M4.6 3.8l1.2 1.3-.6.9c.4.9 1.1 1.6 2 2l.9-.6 1.3 1.2-.7 1c-2.4-.3-4.3-2.2-4.6-4.6z"/></svg>
        (418)-555-0142
      </li>
      <li>
        <svg viewBox="0 0 14 14" aria-hidden="true"><path d="M1.5 7L7 2l5.5 5M3 5.8V12.5h3V9h2v3.5h3V5.8"/></svg>
        www.tarvex-Up.com
      </li>
      <li>
        <svg viewBox="0 0 14 14" aria-hidden="true"><rect x="1" y="3" width="12" height="8.5"/><path d="M1 3l6 5 6-5M1 11.5l4.3-4.3M13 11.5L8.7 7.2"/></svg>
        contact@Tarvex-Up.com
      </li>
    </ul>
  </section>
</main>
</body>
</html>
```